qMerilon - A forward thinking technology company in the greater Silicon Valley

A .ppt slide deck for a software consulting company. This slide deck will be used for project kick off meetings, sales proposals, and presentations to large audiences that report progress on a variety of projects. It should catch the eye with appealing creativity. Allow for flexibility in space and display. Project well both virtually and in person under varying light conditions. The finished product should give the impression that we are a custom shop but balance in appeal to larger, more traditional companies.

Review of the designs has been delayed due to holiday travel. Thank you for your submissions. I look forward to getting back to you the week of December 3rd.

Target Market(s)

We are an innovative technology company in the greater Silicon Valley. We design and build custom business analytics tools for large, retail corporations. Our solutions deal primarily in the supply chain space but we are leaning towards commercial construction and telecommunications industries. We are targeting prospective clients interested in machine learning and artificial intelligence. Our customers know quality and will pay for a custom solution that exceeds their expectations.

Industry/Entity Type

Business Software

Font styles to use
Sans Serif

Colors

Designer to choose colors to be used in the design.

Requirements
Must have
• Color, graphics, and photos. Multiple different template pages to appeal for graphs, pictures, text, or timelines.
Should not have
• Anything that resembles a "fidget spinner."

```html
<!DOCTYPE html>
<html lang="en">
<head>
<meta charset="utf-8">
<title>qMerilon – Presentation Template</title>
<link href="https://fonts.googleapis.com/css2?family=Lato:wght@400;700;900&family=Tinos:wght@400&display=swap" rel="stylesheet">
<style>
:root{
  --green:#8bb24a;
  --green-dark:#76a03a;
  --teal:#2f7f9d;
  --ink:#111418;
  --grey:#e9ebee;
  --line:#dfe3e6;
  --white:#ffffff;
  --photo-a:#5d5f60;
  --photo-b:#b9b3a8;
}
*{box-sizing:border-box;margin:0;padding:0}
html,body{width:1200px;height:2791px;overflow:hidden;background:#fff}
body{font-family:"Lato",Arial,sans-serif;color:var(--ink)}
.deck{width:1200px;height:2791px;display:grid;grid-template-columns:597px 597px;grid-template-rows:repeat(8,1fr);gap:3px 6px;background:var(--grey)}
.slide{position:relative;background:var(--white);overflow:hidden;border-bottom:4px solid #c9dcaa}
.slide.top-rule{border-top:4px solid #c9dcaa}
.title{font-weight:900;font-size:26px;text-align:center;letter-spacing:.2px;text-transform:uppercase}
.rule{width:50px;height:3px;background:var(--teal);margin:8px auto 0}
.rule.green{background:var(--green)}
.body{font-family:"Tinos","Times New Roman",serif;font-size:9.5px;line-height:1.45;color:#222}
.body.j{text-align:justify}
.photo{position:absolute;background:linear-gradient(135deg,var(--photo-a),var(--photo-b))}
.abs{position:absolute}
h4{font-size:11.5px;font-weight:700}
.brand{display:flex;align-items:center;gap:10px}
.brand-mark{width:30px;height:30px;background:var(--teal)}
.brand-name{font-size:40px;font-weight:700;color:var(--teal)}

/* cover */
.cover .photo{inset:0;background:linear-gradient(160deg,#eef0f0,#cfd3d4 60%,#a9aeb0)}
.cover .laptop{left:150px;top:125px;width:290px;height:185px;background:linear-gradient(135deg,#1f3f5a,#2c6a86);border-radius:6px}
.cover .logo-box{left:60px;top:22px;background:rgba(255,255,255,.85);padding:8px 14px}
.cover .tagline{font-size:17px;font-weight:700;color:var(--green-dark);margin-top:4px}

/* about */
.about .text{left:0;top:0;width:300px;height:100%;padding:26px 40px}
.about .photo{left:300px;top:0;width:297px;height:100%;background:linear-gradient(135deg,#3d4144,#b8b2a6 55%,#e5e1da)}
.about .body{margin-top:28px}
.about .body p+p{margin-top:14px}

/* your title */
.ytitle .text{left:60px;top:80px;width:200px}
.ytitle .rule{margin-top:10px}
.ytitle .body{text-align:center;margin-top:24px}
.ytitle .illus{left:355px;top:60px;width:215px;height:155px;background:linear-gradient(135deg,#f4c6d8,#7fb0e6 50%,#f6c97a);border-radius:10px}

/* team */
.team .title{margin-top:16px}
.team .row{position:absolute;top:90px;left:60px;right:60px;display:flex;justify-content:space-around}
.member{width:175px;text-align:center}
.member .name{font-size:11px;font-weight:900}
.member .avatar{width:98px;height:98px;border-radius:50%;margin:8px auto 4px;background:radial-gradient(circle at 50% 40%,#cfd4e8,#6c6fa0)}
.member .avatar.b{background:radial-gradient(circle at 50% 40%,#e9dcd6,#a9b3bf)}
.member .role{font-size:9.5px;font-weight:900}
.member .body{text-align:left;margin-top:8px}

/* timeline */
.time .title{margin-top:24px}
.time .lead{text-align:center;margin:8px 36px 0}
.time svg{position:absolute;left:0;top:120px}
.time text{font-family:"Tinos",serif}

/* three cols */
.cols3 .title{margin-top:12px}
.cols3 .grid{position:absolute;left:32px;right:32px;top:70px;display:grid;grid-template-columns:repeat(3,1fr);gap:18px}
.cols3 .body p+p{margin-top:14px}

/* two cols */
.cols2 .title{margin-top:16px}
.cols2 .grid{position:absolute;left:60px;right:60px;top:120px;display:grid;grid-template-columns:1fr 1fr;gap:24px}
.cols2 .body p+p{margin-top:14px}
.cols2b .title{margin-top:8px;font-size:24px}
.cols2b .photo{left:0;top:45px;width:100%;height:110px;background:linear-gradient(120deg,#1c2329,#3d4a52 55%,#7b6f62)}
.cols2b .band{position:absolute;left:0;right:0;top:130px;height:25px;background:var(--green);text-align:center;font-weight:900;font-size:20px;color:var(--ink);line-height:25px}
.cols2b .grid{top:168px;left:36px;right:36px}

/* boxes */
.boxes .title{margin-top:18px}
.boxes .lead{text-align:center;margin:14px 60px 0}
.boxes .row{position:absolute;left:28px;right:28px;top:150px;display:flex;gap:10px}
.boxes .box{flex:1;height:170px;padding:32px 14px 10px;text-align:center;position:relative}
.box.fill{background:var(--green);color:#fff}
.box.fill .body{color:#fff}
.box.frame{border:2px solid var(--teal);margin-top:-6px;height:176px}
.box .dot{position:absolute;left:50%;top:-2px;transform:translate(-50%,-50%);width:26px;height:26px;border-radius:50%;background:#fff;border:2px solid var(--green)}

/* services */
.services .title{margin-top:12px}
.services .row{position:absolute;left:20px;right:20px;top:68px;display:grid;grid-template-columns:repeat(4,1fr);gap:14px}
.svc .icon{width:66px;height:66px;border-radius:50%;border:1px solid #ccc;margin:0 auto 14px;display:flex;align-items:center;justify-content:center;box-shadow:0 2px 4px rgba(0,0,0,.15)}
.svc h4{font-size:10.5px;margin-bottom:4px}

/* bullets */
.bullets .title{margin-top:18px}
.bullets .grid{position:absolute;left:40px;right:40px;top:100px;display:grid;grid-template-columns:1fr 1fr;gap:24px 22px}
.bul{display:flex;gap:8px}
.bul .dot{flex:none;width:28px;height:28px;border-radius:50%;background:var(--teal)}
.bul .dot.g{background:var(--green)}
.bul .body{margin-top:3px}

/* quote */
.quote .photo{inset:0;background:linear-gradient(135deg,#2a2b2e,#5a5b5d 45%,#9c9ea0)}
.quote .card{position:absolute;left:170px;top:0;width:300px;height:290px;background:#fff;padding:45px 28px 0;text-align:center;box-shadow:0 4px 14px rgba(0,0,0,.3)}
.quote blockquote{font-size:22px;font-weight:700;line-height:1.32}
.quote cite{display:block;margin-top:14px;font-style:normal;font-size:9.5px;color:var(--teal);font-weight:700}

/* six grid */
.six .lead{position:absolute;left:24px;top:50px;width:190px;font-size:25px;font-weight:700;line-height:1.25;text-align:center}
.six .chart{position:absolute;left:70px;top:245px}
.six .grid{position:absolute;left:272px;right:24px;top:36px;display:grid;grid-template-columns:1fr 1fr;gap:20px 16px}
.six h4{font-size:10.5px;margin-bottom:4px}

/* contact */
.contact .photo{left:0;top:0;width:100%;height:175px;background:linear-gradient(135deg,#6b4a33,#a77d5a 45%,#d9cdbd)}
.contact .bottom{position:absolute;left:0;right:0;top:175px;bottom:0;background:#f2f3f3}
.contact .ctitle{position:absolute;left:24px;top:188px;font-size:26px;font-weight:900}
.contact .socials{position:absolute;left:265px;top:155px;display:flex;gap:50px}
.soc{text-align:center}
.soc .c{width:38px;height:38px;border-radius:50%;background:#1f5d9a;margin:0 auto 6px}
.soc .c.t{background:#2f8fd6}
.contact .ways{position:absolute;left:40px;right:40px;top:225px;display:flex;justify-content:space-between}
.way{text-align:center;width:160px}
.way .c{width:64px;height:64px;border-radius:50%;background:#fff;border:1px solid #ccc;margin:0 auto 6px;display:flex;align-items:center;justify-content:center}

/* percent */
.pct .title{margin-top:18px}
.pct .lead{text-align:center;margin:18px 40px 0}
.pct .row{position:absolute;left:30px;right:30px;display:flex;justify-content:space-between;align-items:center}
.pct .big{font-size:24px;font-weight:900;line-height:1.15;text-align:left;margin-right:30px}
.pct .teal{color:var(--teal)}
.pct .green{color:var(--green)}
.pct h4{font-size:10.5px;margin-bottom:6px}

/* thanks */
.thanks .photo{inset:0;background:linear-gradient(135deg,#41484d,#8a8680 45%,#d5d0c6)}
.thanks .bars{position:absolute;left:0;right:0;top:120px}
.thanks .bar{height:14px;background:var(--green);margin-bottom:12px;opacity:.95}
.thanks .brand{position:absolute;left:110px;top:118px}
.thanks .brand-name{font-size:60px;font-weight:900;letter-spacing:1px}
.thanks .brand-mark{width:46px;height:46px}
</style>
</head>
<body>
<main class="deck">

  <section class="slide cover">
    <div class="photo" role="img" aria-label="Photo of a desk with a laptop showing analytics graphics, a mug and office items"></div>
    <div class="abs laptop" role="img" aria-label="Laptop screen with analytics dashboard"></div>
    <div class="abs logo-box">
      <div class="brand"><span class="brand-mark"></span><span class="brand-name">qMerilon</span></div>
      <div class="tagline">Your Partner for Innovative Software Solutions</div>
    </div>
  </section>

  <section class="slide about">
    <div class="abs text">
      <h2 class="title">About us</h2>
      <div class="rule"></div>
      <div class="body">
        <p>Lorem ipsum dolor sit amet, consectetur adipiscing elit, sed do eiusmod tempor incididunt ut labore et dolore magna aliqua. Ut enim ad minim veniam, quis nostrud exercitation ullamco laboris nisi ut aliquip ex ea commodo consequat. Excepteur sint occaecat cupidatat non proident, sunt in culpa qui officia deserunt mollit anim id est laborum.</p>
        <p>Lorem ipsum dolor sit amet, consectetur adipiscing elit, sed do eiusmod tempor incididunt ut labore et dolore magna aliqua. Ut enim ad minim veniam, quis nostrud exercitation ullamco laboris nisi ut aliquip ex ea commodo consequat. Duis aute irure dolor in reprehenderit.</p>
      </div>
    </div>
    <div class="photo" role="img" aria-label="Photo of hands typing on a laptop beside a coffee cup"></div>
  </section>

  <section class="slide top-rule ytitle">
    <div class="abs text">
      <h2 class="title">Your title</h2>
      <div class="rule green"></div>
      <p class="body">Lorem ipsum dolor sit amet, consectetur adipiscing elit, sed do eiusmod tempor incididunt ut labore et dolore magna aliqua.</p>
    </div>
    <div class="abs illus" role="img" aria-label="Isometric illustration of a digital workspace with charts and people"></div>
  </section>

  <section class="slide team">
    <h2 class="title">Our team</h2>
    <div class="rule"></div>
    <div class="row">
      <div class="member">
        <div class="name">RAVI K.</div>
        <div class="avatar" role="img" aria-label="Portrait avatar of the CEO"></div>
        <div class="role">CEO</div>
        <p class="body">Lorem ipsum dolor sit amet, consectetur adipiscing elit, sed do eiusmod tempor incididunt ut labore et dolore magna aliqua.</p>
      </div>
      <div class="member">
        <div class="name">LENA P.</div>
        <div class="avatar b" role="img" aria-label="Portrait avatar of the manager"></div>
        <div class="role">MANAGER</div>
        <p class="body">Lorem ipsum dolor sit amet, consectetur adipiscing elit, sed do eiusmod tempor incididunt ut labore et dolore magna aliqua.</p>
      </div>
    </div>
  </section>

  <section class="slide top-rule time">
    <h2 class="title">Our comapy in the time</h2>
    <p class="body lead">Lorem ipsum dolor sit amet, consectetur adipiscing elit, sed do eiusmod tempor incididunt ut labore et dolore magna aliqua. Ut enim ad minim veniam, quis nostrud exercitation ullamco laboris nisi ut aliquip ex ea commodo consequat.</p>
    <svg width="597" height="210" viewBox="0 0 597 210">
      <line x1="8" y1="105" x2="560" y2="105" stroke="#bfc4c8" stroke-width="3"/>
      <circle cx="8" cy="105" r="4" fill="#bfc4c8"/><circle cx="560" cy="105" r="4" fill="#bfc4c8"/>
      <g font-size="9" fill="#222" text-anchor="middle">
        <g><circle cx="42" cy="105" r="22" fill="#fff" stroke="#8bb24a" stroke-width="4"/><text x="42" y="75" font-family="Lato" font-weight="900" font-size="13" fill="#8bb24a">2015</text><line x1="42" y1="127" x2="42" y2="140" stroke="#8bb24a" stroke-width="2"/><text x="42" y="152">Add Text</text><text x="42" y="164">Lorem ipsum dolor sit</text></g>
        <g><circle cx="160" cy="105" r="22" fill="#fff" stroke="#2f7f9d" stroke-width="4"/><text x="160" y="145" font-family="Lato" font-weight="900" font-size="13" fill="#2f7f9d">2016</text><line x1="160" y1="83" x2="160" y2="65" stroke="#2f7f9d" stroke-width="2"/><text x="160" y="38">Add Text</text><text x="160" y="50">Lorem ipsum dolor sit</text></g>
        <g><circle cx="278" cy="105" r="22" fill="#fff" stroke="#8bb24a" stroke-width="4"/><text x="278" y="75" font-family="Lato" font-weight="900" font-size="13" fill="#8bb24a">2017</text><line x1="278" y1="127" x2="278" y2="140" stroke="#8bb24a" stroke-width="2"/><text x="278" y="152">Add Text</text><text x="278" y="164">Lorem ipsum dolor sit</text></g>
        <g><circle cx="396" cy="105" r="22" fill="#fff" stroke="#2f7f9d" stroke-width="4"/><text x="396" y="145" font-family="Lato" font-weight="900" font-size="13" fill="#2f7f9d">2018</text><line x1="396" y1="83" x2="396" y2="65" stroke="#2f7f9d" stroke-width="2"/><text x="396" y="38">Add Text</text><text x="396" y="50">Lorem ipsum dolor sit</text></g>
        <g><circle cx="514" cy="105" r="22" fill="#fff" stroke="#8bb24a" stroke-width="4"/><text x="514" y="75" font-family="Lato" font-weight="900" font-size="13" fill="#8bb24a">2019</text><line x1="514" y1="127" x2="514" y2="140" stroke="#8bb24a" stroke-width="2"/><text x="514" y="152">Add Text</text><text x="514" y="164">Lorem ipsum dolor sit</text></g>
      </g>
    </svg>
  </section>

  <section class="slide top-rule cols3">
    <h2 class="title">Three columns text</h2>
    <div class="rule"></div>
    <div class="grid">
      <div class="body j"><p>Lorem ipsum dolor sit amet, consectetur adipiscing elit, sed do eiusmod tempor incididunt ut labore et dolore magna aliqua. Ut enim ad minim veniam, quis nostrud exercitation ullamco laboris nisi ut aliquip ex ea commodo consequat.</p><p>Duis aute irure dolor in reprehenderit in voluptate velit esse cillum dolore eu fugiat nulla pariatur. Excepteur sint occaecat cupidatat non proident, sunt in.</p></div>
      <div class="body j"><p>Culpa qui officia deserunt mollit anim id est laborum.</p><p>Lorem ipsum dolor sit amet, consectetur adipiscing elit, sed do eiusmod tempor incididunt ut labore et dolore magna aliqua. Ut enim ad minim veniam, quis nostrud exercitation ullamco laboris nisi.</p><p>Duis aute irure dolor in reprehenderit in voluptate velit esse cillum dolore eu fugiat nulla pariatur. Excepteur sint.</p></div>
      <div class="body j"><p>Occaecat cupidatat non proident, sunt in culpa qui officia deserunt mollit anim id est laborum.</p><p>Lorem ipsum dolor sit amet, consectetur adipiscing elit, sed do eiusmod tempor incididunt ut labore et dolore magna aliqua. Ut enim ad minim veniam, quis nostrud exercitation ullamco laboris nisi ut aliquip.</p></div>
    </div>
  </section>

  <section class="slide cols2">
    <h2 class="title">Two columns text</h2>
    <div class="rule"></div>
    <div class="grid">
      <div class="body j"><p>Lorem ipsum dolor sit amet, consectetur adipiscing elit, sed do eiusmod tempor incididunt ut labore et dolore magna aliqua. Ut enim ad minim veniam, quis nostrud exercitation ullamco laboris nisi ut aliquip ex ea commodo consequat.</p><p>Duis aute irure dolor in reprehenderit in voluptate velit esse cillum dolore eu fugiat nulla pariatur. Lorem ipsum dolor sit.</p></div>
      <div class="body j"><p>Amet, consectetur adipiscing elit, sed do eiusmod tempor incididunt ut labore et dolore magna aliqua. Ut enim ad minim veniam, quis nostrud exercitation ullamco laboris nisi ut aliquip ex ea commodo consequat.</p><p>Duis aute irure dolor in reprehenderit in voluptate velit esse cillum dolore eu fugiat nulla pariatur.</p></div>
    </div>
  </section>

  <section class="slide cols2 cols2b">
    <h2 class="title">Two columns text and picture</h2>
    <div class="photo" role="img" aria-label="Photo of a hand over a laptop showing lines of code"></div>
    <div class="band">YOUR TITLE</div>
    <div class="grid">
      <div class="body j"><p>Lorem ipsum dolor sit amet, consectetur adipiscing elit, sed do eiusmod tempor incididunt ut labore et dolore magna aliqua. Ut enim ad minim veniam, quis nostrud exercitation ullamco laboris nisi ut aliquip ex ea commodo consequat.</p><p>Duis aute irure dolor in reprehenderit in voluptate velit esse cillum dolore eu fugiat nulla pariatur. Lorem ipsum dolor sit.</p></div>
      <div class="body j"><p>Amet, consectetur adipiscing elit, sed do eiusmod tempor incididunt ut labore et dolore magna aliqua. Ut enim ad minim veniam, quis nostrud exercitation ullamco laboris nisi ut aliquip ex ea commodo consequat.</p><p>Duis aute irure dolor in reprehenderit in voluptate velit esse cillum dolore eu fugiat nulla pariatur.</p></div>
    </div>
  </section>

  <section class="slide boxes">
    <h2 class="title">Write here a title</h2>
    <div class="rule"></div>
    <p class="body lead">Lorem ipsum dolor sit amet, consectetur adipiscing elit, sed do eiusmod tempor incididunt ut labore et dolore magna aliqua.</p>
    <div class="row">
      <div class="box fill"><span class="dot"></span><p class="body">Lorem ipsum dolor sit amet, consectetur adipiscing elit, sed do eiusmod tempor incididunt ut labore et dolore magna aliqua. Ut enim ad minim veniam, quis nostrud exercitation ullamco laboris nisi ut aliquip ex ea commodo consequat.</p></div>
      <div class="box frame"><span class="dot" style="border-color:var(--teal)"></span><p class="body">Lorem ipsum dolor sit amet, consectetur adipiscing elit, sed do eiusmod tempor incididunt ut labore et dolore magna aliqua. Ut enim ad minim veniam, quis nostrud exercitation ullamco laboris nisi ut aliquip ex ea commodo consequat.</p></div>
      <div class="box fill"><span class="dot"></span><p class="body">Lorem ipsum dolor sit amet, consectetur adipiscing elit, sed do eiusmod tempor incididunt ut labore et dolore magna aliqua. Ut enim ad minim veniam, quis nostrud exercitation ullamco laboris nisi ut aliquip ex ea commodo consequat.</p></div>
    </div>
  </section>

  <section class="slide services">
    <h2 class="title">Our services</h2>
    <div class="rule"></div>
    <div class="row">
      <div class="svc"><div class="icon"><svg width="30" height="30" viewBox="0 0 30 30" fill="none" stroke="#333" stroke-width="2"><rect x="4" y="5" width="22" height="15" rx="1"/><path d="M11 25h8M15 20v5"/><circle cx="15" cy="12.5" r="3.5"/></svg></div><h4>Write Here a Title</h4><p class="body">Lorem ipsum dolor sit amet, consectetur adipiscing elit, sed do eiusmod tempor incididunt ut labore et dolore magna aliqua. Lorem ipsum dolor sit amet, consectetur adipiscing elit, sed do eiusmod tempor incididunt ut labore et dolore magna aliqua.</p></div>
      <div class="svc"><div class="icon"><svg width="30" height="30" viewBox="0 0 30 30" fill="none" stroke="#333" stroke-width="2"><circle cx="11" cy="17" r="6"/><circle cx="11" cy="17" r="2"/><circle cx="21" cy="9" r="4"/><circle cx="21" cy="9" r="1.3"/></svg></div><h4>Write Here a Title</h4><p class="body">Lorem ipsum dolor sit amet, consectetur adipiscing elit, sed do eiusmod tempor incididunt ut labore et dolore magna aliqua. Ut enim ad minim veniam.</p></div>
      <div class="svc"><div class="icon"><svg width="30" height="30" viewBox="0 0 30 30" fill="none" stroke="#333" stroke-width="2"><rect x="4" y="5" width="22" height="15" rx="1"/><path d="M11 25h8M15 20v5M7 16l5-5 4 3 6-6"/></svg></div><h4>Write Here a Title</h4><p class="body">Lorem ipsum dolor sit amet, consectetur adipiscing elit, sed do eiusmod tempor incididunt ut labore et.</p></div>
      <div class="svc"><div class="icon"><svg width="30" height="30" viewBox="0 0 30 30" fill="none" stroke="#333" stroke-width="2"><rect x="7" y="4" width="16" height="22" rx="1"/><path d="M11 10h8M11 14h8M11 18h4"/><circle cx="22" cy="23" r="4" fill="#333"/></svg></div><h4>Write Here a Title</h4><p class="body">Lorem ipsum dolor sit amet, consectetur adipiscing elit, sed do eiusmod tempor incididunt ut labore et dolore magna aliqua. Ut enim ad minim veniam, quis nostrud exercitation.</p></div>
    </div>
  </section>

  <section class="slide bullets">
    <h2 class="title">Write here a title</h2>
    <div class="rule"></div>
    <div class="grid">
      <div class="bul"><span class="dot"></span><div><h4>Write Here a Title</h4><p class="body">Lorem ipsum dolor sit amet, commodo lacinia dignissim vel sed ut volutpat augue phasellus nisi. Parturient eros at in sit erat vehicula, ac vitae non non vestibulum justo.</p></div></div>
      <div class="bul"><span class="dot g"></span><div><h4>Write Here a Title</h4><p class="body">Lorem ipsum dolor sit amet, commodo lacinia dignissim vel sed ut volutpat augue phasellus nisi. Parturient eros at in sit erat vehicula, ac vitae non non vestibulum justo.</p></div></div>
      <div class="bul"><span class="dot g"></span><div><h4>Write Here a Title</h4><p class="body">Lorem ipsum dolor sit amet, commodo lacinia dignissim vel sed ut volutpat augue phasellus nisi. Parturient eros at in sit erat vehicula, ac vitae non non vestibulum justo.</p></div></div>
      <div class="bul"><span class="dot"></span><div><h4>Write Here a Title</h4><p class="body">Lorem ipsum dolor sit amet, commodo lacinia dignissim vel sed ut volutpat augue phasellus nisi. Parturient eros at in sit erat vehicula, ac vitae non non vestibulum justo.</p></div></div>
    </div>
  </section>

  <section class="slide quote">
    <div class="photo" role="img" aria-label="Photo of a desk with printed charts, a laptop and a person writing"></div>
    <div class="card">
      <blockquote>“Be who you are and say what you feel, because those who mind don't matter, and those who matter don't mind.”</blockquote>
      <cite>Adele R. Winslow</cite>
    </div>
  </section>

  <section class="slide six">
    <p class="lead">Lorem ipsum dolor sit amet, consectetur adipiscing elit</p>
    <svg class="chart" width="50" height="50" viewBox="0 0 50 50" fill="none" stroke-width="2"><rect x="4" y="6" width="42" height="30" stroke="#555"/><path d="M10 30l10-10 8 6 12-14" stroke="#8bb24a"/><path d="M25 36v8M17 48l8-4 8 4" stroke="#555"/></svg>
    <div class="grid">
      <div><h4>Write Here a Title</h4><p class="body">Lorem ipsum dolor sit amet, consectetur adipiscing elit, sed do eiusmod tempor.</p></div>
      <div><h4>Write Here a Title</h4><p class="body">Lorem ipsum dolor sit amet, consectetur adipiscing elit, sed do eiusmod tempor.</p></div>
      <div><h4>Write Here a Title</h4><p class="body">Lorem ipsum dolor sit amet, consectetur adipiscing elit, sed do eiusmod tempor.</p></div>
      <div><h4>Write Here a Title</h4><p class="body">Lorem ipsum dolor sit amet, consectetur adipiscing elit, sed do eiusmod tempor.</p></div>
      <div><h4>Write Here a Title</h4><p class="body">Lorem ipsum dolor sit amet, consectetur adipiscing elit, sed do eiusmod tempor.</p></div>
      <div><h4>Write Here a Title</h4><p class="body">Lorem ipsum dolor sit amet, consectetur adipiscing elit, sed do eiusmod tempor.</p></div>
    </div>
  </section>

  <section class="slide contact">
    <div class="photo" role="img" aria-label="Photo of a handshake over a desk with documents and a laptop"></div>
    <div class="bottom"></div>
    <h2 class="ctitle">CONTACT US</h2>
    <div class="socials">
      <div class="soc"><div class="c"></div><span class="body">Write your text</span></div>
      <div class="soc"><div class="c"></div><span class="body">Write your text</span></div>
      <div class="soc"><div class="c t"></div><span class="body">Write your text</span></div>
    </div>
    <div class="ways">
      <div class="way"><div class="c"><svg width="26" height="26" viewBox="0 0 24 24" fill="none" stroke="#444" stroke-width="1.6"><path d="M5 3h4l2 5-2.5 1.5a11 11 0 0 0 6 6L16 13l5 2v4a2 2 0 0 1-2 2A16 16 0 0 1 3 5a2 2 0 0 1 2-2z"/></svg></div><span class="body">+1 408 555 0142</span></div>
      <div class="way"><div class="c"><svg width="26" height="26" viewBox="0 0 24 24" fill="none" stroke="#444" stroke-width="1.6"><rect x="3" y="5" width="18" height="14" rx="1"/><path d="M3 6l9 7 9-7"/></svg></div><span class="body">Company e-mail</span></div>
      <div class="way"><div class="c"><svg width="26" height="26" viewBox="0 0 24 24" fill="none" stroke="#444" stroke-width="1.6"><circle cx="12" cy="12" r="9"/><path d="M3 12h18M12 3c3 3 3 15 0 18M12 3c-3 3-3 15 0 18"/></svg></div><span class="body">https://qmerilonlabs.com</span></div>
    </div>
  </section>

  <section class="slide pct">
    <h2 class="title">Percent with graphics</h2>
    <div class="rule"></div>
    <p class="body lead">Lorem ipsum dolor sit amet, consectetur adipiscing elit, sed do eiusmod tempor. Lorem ipsum dolor sit amet, consectetur adipiscing elit.</p>
    <div class="row" style="top:140px">
      <div><h4>Write Here a Title</h4>
        <svg width="200" height="40" viewBox="0 0 200 40">
          <defs><g id="pers"><circle cx="9" cy="5" r="4.5"/><rect x="3" y="11" width="12" height="15" rx="3"/><rect x="4" y="24" width="4" height="14"/><rect x="10" y="24" width="4" height="14"/></g></defs>
          <g fill="#8bb24a"><use href="#pers"/><use href="#pers" x="20"/><use href="#pers" x="40"/><use href="#pers" x="60"/><use href="#pers" x="80"/><use href="#pers" x="100"/><use href="#pers" x="120"/></g>
          <g fill="#cfd3d6"><use href="#pers" x="140"/><use href="#pers" x="160"/><use href="#pers" x="180"/></g>
        </svg>
      </div>
      <div class="big"><span class="teal">70% WOMAN</span><br><span class="green">30 % MEN</span></div>
    </div>
    <div class="row" style="top:240px">
      <div><h4>Write Here a Title</h4>
        <svg width="200" height="40" viewBox="0 0 200 40">
          <g fill="#2f7f9d"><use href="#pers"/><use href="#pers" x="20"/><use href="#pers" x="40"/><use href="#pers" x="60"/><use href="#pers" x="80"/><use href="#pers" x="100"/></g>
          <g fill="#cfd3d6"><use href="#pers" x="120"/><use href="#pers" x="140"/><use href="#pers" x="160"/><use href="#pers" x="180"/></g>
        </svg>
      </div>
      <div class="big"><span class="teal">60% WOMAN</span><br><span class="green">40 % MEN</span></div>
    </div>
  </section>

  <section class="slide thanks">
    <div class="photo" role="img" aria-label="Photo of people working together at a laptop in an office"></div>
    <div class="bars"><div class="bar"></div><div class="bar"></div><div class="bar"></div></div>
    <div class="brand"><span class="brand-mark"></span><span class="brand-name">THANKS</span></div>
  </section>

</main>
</body>
</html>
```